Business Card for Fashion House

We need a business card design for our personalize fashion service for our customers. the business card should reflect reliability, luxury and creativity.
The brand Gravetto is extracted from "Graceful Velvetto"; Gravetto provides fashion designs sprinkled with luxury and style tailored for our elite clients character profile.
Gravetto is created for those who embody class and elegance with a passion for style.
Target Market(s)
Affluent Customers
Industry/Entity Type
Fashion
Contact Information for Business Card
Samira Haddadin
Fashion Designer
Telephone: +971 4 555 0192
Mobile +971 50 555 0147
Emal info@gravetto-example.com
Website www.gravetto-example.com
Social Media Youtube g+ Facebook Instagram Pin /gravetto
Font styles to use
Other font styles liked:
- Audrey provided
Look and feel
Each slider illustrates characteristics of the customer's brand and the style your logo design should communicate.

```html
<!DOCTYPE html>
<html lang="en">
<head>
<meta charset="utf-8">
<title>Gravetto — Business Card</title>
<link href="https://fonts.googleapis.com/css2?family=Marcellus&display=swap" rel="stylesheet">
<style>
  :root {
    --backdrop: #141414;
    --card-deep: #050505;
    --card-lift: #1c1c1c;
    --ink: #f2f2f2;
    --ink-soft: #bdbdbd;
    --icon: #d8d8d8;
  }
  * { margin: 0; padding: 0; box-sizing: border-box; }
  html, body {
    width: 1200px;
    height: 864px;
    overflow: hidden;
    background: var(--backdrop);
    font-family: "Marcellus", "Optima", serif;
    color: var(--ink);
  }
  .canvas {
    position: relative;
    width: 1200px;
    height: 864px;
    display: flex;
    align-items: center;
    justify-content: center;
    gap: 60px;
  }
  .card {
    position: relative;
    width: 510px;
    height: 292px;
    border-radius: 4px;
    overflow: hidden;
    background:
      linear-gradient(160deg, var(--card-lift) 0%, var(--card-deep) 45%, var(--card-deep) 70%, #151515 100%);
    box-shadow: 0 20px 40px rgba(0,0,0,0.55);
  }

  /* Contact side */
  .card-back .brand {
    position: absolute;
    top: 34px;
    left: 40px;
    width: 180px;
    display: flex;
    flex-direction: column;
    align-items: center;
  }
  .brand-square {
    width: 26px;
    height: 26px;
    border: 3px solid var(--ink);
    transform: rotate(45deg);
    margin-bottom: 22px;
  }
  .card-back .brand-name {
    font-size: 17px;
    letter-spacing: 0.42em;
    padding-left: 0.42em;
    text-transform: uppercase;
  }
  .holder {
    position: absolute;
    top: 128px;
    left: 40px;
    width: 180px;
    text-align: center;
  }
  .holder-name {
    font-size: 15px;
    letter-spacing: 0.03em;
    text-transform: uppercase;
  }
  .holder-role {
    font-size: 11px;
    color: var(--ink-soft);
    margin-top: 1px;
  }
  .contacts {
    position: absolute;
    top: 188px;
    left: 26px;
    list-style: none;
  }
  .contacts li {
    display: flex;
    align-items: center;
    gap: 9px;
    height: 19px;
    font-size: 12px;
    letter-spacing: 0.04em;
  }
  .contacts li.small { font-size: 10.5px; }
  .contacts svg { width: 11px; height: 11px; flex: none; }

  /* Brand side */
  .card-front .brand-mark {
    position: absolute;
    top: 50%;
    left: 50%;
    transform: translate(-50%, -50%);
    display: flex;
    align-items: center;
    gap: 26px;
  }
  .card-front .brand-square {
    width: 38px;
    height: 38px;
    border-width: 4px;
    margin: 0;
  }
  .card-front .brand-name {
    font-size: 26px;
    letter-spacing: 0.42em;
    text-transform: uppercase;
  }
</style>
</head>
<body>
<main class="canvas">

  <section class="card card-back" aria-label="Contact side">
    <div class="brand">
      <span class="brand-square" aria-hidden="true"></span>
      <span class="brand-name">Gravetto</span>
    </div>
    <div class="holder">
      <p class="holder-name">Samira Haddadin</p>
      <p class="holder-role">Fashion Designer</p>
    </div>
    <ul class="contacts">
      <li>
        <svg viewBox="0 0 12 12" aria-hidden="true"><circle cx="6" cy="6" r="5.3" fill="none" stroke="var(--icon)" stroke-width="1"/><path d="M3.6 4.6c0-.7.5-1.1 2.4-1.1s2.4.4 2.4 1.1v.5H7.3v-.6H4.7v.6H3.6zM4.4 5.6h3.2l.6 2.6H3.8z" fill="var(--icon)"/></svg>
        +971 4 555 0192
      </li>
      <li>
        <svg viewBox="0 0 12 12" aria-hidden="true"><circle cx="6" cy="6" r="5.3" fill="none" stroke="var(--icon)" stroke-width="1"/><rect x="4.3" y="2.8" width="3.4" height="6.4" rx=".6" fill="none" stroke="var(--icon)" stroke-width=".9"/><circle cx="6" cy="8.1" r=".45" fill="var(--icon)"/></svg>
        +971 50 555 0147
      </li>
      <li class="small">
        <svg viewBox="0 0 12 12" aria-hidden="true"><circle cx="6" cy="6" r="5.3" fill="none" stroke="var(--icon)" stroke-width="1"/><rect x="3.2" y="4" width="5.6" height="4" fill="none" stroke="var(--icon)" stroke-width=".9"/><path d="M3.3 4.1 6 6.2l2.7-2.1" fill="none" stroke="var(--icon)" stroke-width=".9"/></svg>
        info@gravetto-example.com
      </li>
      <li class="small">
        <svg viewBox="0 0 12 12" aria-hidden="true"><circle cx="6" cy="6" r="5.3" fill="none" stroke="var(--icon)" stroke-width="1"/><circle cx="6" cy="6" r="3" fill="none" stroke="var(--icon)" stroke-width=".8"/><path d="M3 6h6M6 3c-1.4 1.6-1.4 4.4 0 6M6 3c1.4 1.6 1.4 4.4 0 6" fill="none" stroke="var(--icon)" stroke-width=".7"/></svg>
        www.gravetto-example.com
      </li>
    </ul>
  </section>

  <section class="card card-front" aria-label="Brand side">
    <div class="brand-mark">
      <span class="brand-square" aria-hidden="true"></span>
      <span class="brand-name">Gravetto</span>
    </div>
  </section>

</main>
</body>
</html>
```